Asphalt Driveway Billboard Design

We need a billboard designed for an Asphalt & Concrete Company in Minnesota. We want to advertise Asphalt Driveways on this billboard! Logo is uploaded below. Our website is pinecrest-paving.com for more information.

```html
<!DOCTYPE html>
<html lang="en">
<head>
<meta charset="utf-8">
<title>Asphalt Driveway Billboard</title>
<link href="https://fonts.googleapis.com/css2?family=Montserrat:ital,wght@0,800;1,800;1,900&display=swap" rel="stylesheet">
<style>
  :root {
    --page: #eef1f4;
    --panel: #2a2b2e;
    --panel-deep: #07101d;
    --white: #ffffff;
    --brand-blue: #1a9ad6;
    --bright-blue: #0a8fe0;
    --navy: #1b3a9a;
    --photo-sky: #6d6e70;
    --photo-house: #8a8478;
    --photo-drive: #b9bcbd;
    --photo-lawn: #5f7f3a;
  }
  html, body {
    margin: 0;
    width: 1200px;
    height: 1068px;
    overflow: hidden;
    background: var(--page);
  }
  .billboard {
    position: absolute;
    left: 0;
    top: 358px;
    width: 1200px;
    height: 351px;
    background: var(--panel);
    overflow: hidden;
    font-family: "Montserrat", sans-serif;
  }
  .billboard__art {
    position: absolute;
    inset: 0;
  }
  .headline {
    position: absolute;
    left: 34px;
    top: 40px;
    margin: 0;
    font-weight: 900;
    font-style: italic;
    line-height: 1;
    letter-spacing: 1px;
    text-transform: uppercase;
  }
  .headline__line { display: block; }
  .headline__line--white { color: var(--white); font-size: 68px; }
  .headline__line--blue { color: var(--brand-blue); font-size: 72px; margin-top: 2px; }
  .headline__line--small { color: var(--white); font-size: 62px; margin-top: 4px; }
  .website {
    position: absolute;
    left: 36px;
    top: 283px;
    margin: 0;
    color: var(--white);
    font-weight: 900;
    font-style: italic;
    font-size: 26px;
    letter-spacing: 0.5px;
    text-transform: uppercase;
  }
  .brand {
    position: absolute;
    right: 24px;
    bottom: 12px;
    text-align: center;
    color: var(--white);
    font-weight: 800;
    text-transform: uppercase;
    line-height: 1.1;
  }
  .brand__name { display: block; font-size: 30px; letter-spacing: 1px; }
  .brand__tag { display: block; font-size: 10px; letter-spacing: 1.5px; }
</style>
</head>
<body>
  <section class="billboard">
    <svg class="billboard__art" width="1200" height="351" viewBox="0 0 1200 351" aria-hidden="false">
      <defs>
        <linearGradient id="photoTone" x1="0" y1="0" x2="0" y2="1">
          <stop offset="0" stop-color="var(--photo-sky)"/>
          <stop offset="0.38" stop-color="var(--photo-house)"/>
          <stop offset="0.62" stop-color="var(--photo-drive)"/>
          <stop offset="1" stop-color="var(--photo-lawn)"/>
        </linearGradient>
        <linearGradient id="photoFade" x1="0" y1="0" x2="1" y2="0">
          <stop offset="0" stop-color="var(--panel)" stop-opacity="1"/>
          <stop offset="0.3" stop-color="var(--panel)" stop-opacity="0"/>
        </linearGradient>
      </defs>
      <g role="img" aria-label="Photo of a brick house with a two-door garage, a freshly paved driveway and green lawn">
        <rect class="photo" x="540" y="0" width="660" height="351" fill="url(#photoTone)"/>
        <rect x="540" y="0" width="660" height="351" fill="url(#photoFade)"/>
      </g>
      <polygon class="dark-slash" points="424,0 555,0 740,351 635,351" fill="var(--panel-deep)" opacity="0.85"/>
      <polygon class="blue-slash" points="490,63 610,63 784,351 675,351" fill="var(--bright-blue)" opacity="0.75"/>
      <polygon class="navy-slash" points="569,166 722,166 786,351 640,351" fill="var(--navy)" opacity="0.8"/>
    </svg>

    <h1 class="headline">
      <span class="headline__line headline__line--white">Asphalt</span>
      <span class="headline__line headline__line--blue">Driveway</span>
      <span class="headline__line headline__line--small">Specialists</span>
    </h1>
    <p class="website">www.pinecrest-paving.com</p>

    <div class="brand">
      <span class="brand__name">Pinecrest</span>
      <span class="brand__tag">Asphalt &amp; Concrete</span>
    </div>
  </section>
</body>
</html>
```